Flyer Design Project for Sports Medicine Services

I am a sports medicine doctor specialising in the diagnosis and management of sport and exercise injuries for all ages and levels of activity - from elite to weekend jogger. I work under the Business name Peak Stride Athletics and do have a company logo. I am wanting a flier that I can send to family doctors, physiotherapists and sports clubs explaining who I am what I can offer and why they should send me patients.
- I have a Masters in Sports Medicine (MSportsMed), Diplomas in Obstetrics/Gynaecology (DRANZCOG) and also Paediatrics (DCH) and certificate in advanced clinical hypnosis
-accurate diagnosis and management plan with their regular physio to return the player / athlete to the field / court /gym as soon as safely possible
-hypnosis for sports performance eg anxiety control, confidence and mental rehearsal for individuals and teams
- because there are many possible therapists and therapy options, as a sports doctor I can work out who they need to see a physiotherapist, surgeon, massage therapist chiropractor or podiatrist to return them to activity or whether cortisone, PRP or autologous blood injections are needed
-can provide one point of contact for coaches and clubs for rehabilitation and return to sport advice.
- work with Laura Pemberton ex Australian Athlete, a Performance Strategist (NLB listed resource person) and registered Psychologist for best mental preparation for individuals teams and coach development
- can organise rapid access to MRI, ultrasound and specialist appointments if needed
-I work at 3 practices KinetaCare 518 Hollis Rd Hollis 84619027 Monday Wednesday Friday; Brackley Sports Clinic, 193 Brackley Rd, Adelaide 81946372 Tuesday Riverton Hawks Sports Medicine Clinic, Tolvane Arena 8162 5907 Thursday.
-facebook site peakstrideathletics
Updates
Hi All, just to clarify.. My name is Simon Drewett and I am the sports doctor. My wife is Laura Pemberton and she is the psychologist. The flier should mainly be advertising my sports medicine services and a byline ( or at least not the first line in the title) about the Performance Strategy and Coach development.
Target Market(s)
family doctors (GPs), Sporting Clubs, Physiotherapists
Industry/Entity Type
Massage
Look and feel

```html
<!DOCTYPE html>
<html lang="en">
<head>
<meta charset="utf-8">
<title>Peak Stride Athletics – Sports Medicine Flyer</title>
<link rel="stylesheet" href="https://fonts.googleapis.com/css2?family=Jost:wght@400;500;600&family=Arimo:wght@700&display=swap">
<style>
  :root {
    --lime: #b3d334;
    --lime-pale: #dbe9a3;
    --sky: #29a8e0;
    --navy: #0f2446;
    --ink: #1c1c1c;
    --white: #ffffff;
    --skin-light: #f4cfb2;
    --skin-mid: #e9ac84;
    --skin-deep: #c9845e;
  }
  * { box-sizing: border-box; margin: 0; padding: 0; }
  html, body { width: 863px; height: 1200px; overflow: hidden; background: var(--white); }
  .flyer { position: relative; width: 863px; height: 1200px; font-family: "Jost", sans-serif; overflow: hidden; }

  .hero-photo {
    position: absolute; left: 0; top: 0; width: 863px; height: 713px;
    background:
      radial-gradient(ellipse 260px 160px at 560px 420px, var(--skin-mid), transparent 70%),
      radial-gradient(ellipse 380px 120px at 420px 600px, var(--skin-deep), transparent 75%),
      radial-gradient(ellipse 320px 200px at 160px 480px, var(--skin-light), transparent 70%),
      radial-gradient(ellipse 280px 220px at 760px 330px, var(--skin-mid), transparent 70%),
      linear-gradient(180deg, #fbf4ee 0%, #f6e2d2 70%, #ead0bc 100%);
  }

  .header-band { position: absolute; top: 63px; left: 35px; right: 0; height: 205px; display: flex; }
  .brand-box {
    width: 246px; background: var(--white);
    display: flex; flex-direction: column; align-items: center; justify-content: center; gap: 14px;
  }
  .brand-mark { width: 64px; height: 64px; border-radius: 50%; background: var(--sky); }
  .brand-name {
    font-weight: 600; font-size: 27px; line-height: 1.05; color: var(--sky); text-align: center;
  }
  .title-box {
    flex: 1; padding: 16px 0 0 18px;
    background: linear-gradient(90deg, var(--lime-pale) 0%, rgba(219,233,163,0.92) 70%, rgba(219,233,163,0.75) 100%);
  }
  .headline {
    font-family: "Arimo", sans-serif; font-weight: 700; font-size: 38px; line-height: 49px; color: var(--ink);
  }

  .info-panel { position: absolute; left: 0; top: 713px; width: 863px; height: 370px; background: var(--lime); padding: 24px 64px 0 48px; color: var(--white); }
  .intro { font-weight: 600; font-size: 19.5px; line-height: 27px; }
  .credentials { list-style: none; margin-top: 22px; }
  .credentials li {
    position: relative; padding-left: 26px; font-size: 15px; line-height: 20px; text-align: justify; margin-bottom: 20px;
  }
  .credentials li::before {
    content: ""; position: absolute; left: 3px; top: 6px; width: 9px; height: 9px; border-radius: 50%; background: var(--sky);
  }

  .locations { position: absolute; left: 0; top: 1083px; width: 863px; height: 90px; background: var(--sky); }
  .location-list { position: absolute; left: 48px; top: 8px; list-style: none; color: var(--navy); font-size: 14.5px; line-height: 25px; }
  .location-list strong { font-weight: 600; }
  .brand-tile {
    position: absolute; left: 720px; top: 3px; width: 103px; height: 84px; background: var(--white);
    display: flex; flex-direction: column; align-items: center; justify-content: center; gap: 6px;
  }
  .brand-tile .brand-mark { width: 24px; height: 24px; }
  .brand-tile .brand-name { font-size: 12.5px; }

  .footer-strip { position: absolute; left: 0; top: 1173px; width: 863px; height: 27px; background: var(--lime); }
</style>
</head>
<body>
<main class="flyer">
  <div class="hero-photo" role="img" aria-label="Photo of a therapist's hands massaging an athlete's calf"></div>

  <header class="header-band">
    <div class="brand-box">
      <span class="brand-mark"></span>
      <span class="brand-name">Peak Stride<br>Athletics</span>
    </div>
    <div class="title-box">
      <h1 class="headline">Sports and Exercise<br>Injury Diagnosis<br>Elite Coach Development</h1>
    </div>
  </header>

  <section class="info-panel">
    <p class="intro">Simon Drewett a Sports Medicine and Exercise Injuries Doctor specialising in the diagnosis and management of sport and exercise injuries for all ages and levels of activity - from elite to weekend jogger.</p>
    <ul class="credentials">
      <li>Simon has a Masters in Sports Medicine (MSportsMed), Diplomas in Obstetrics /Gynaecology (DRANZCOG) and also Paediatrics (DCH) and certificate in advanced clinical hypnosis</li>
      <li>Accurate diagnosis and management plan with their regular physio to return the player / athlete to the field / court /gym as soon as safely possible</li>
      <li>Hypnosis for sports performance eg anxiety control, confidence and mental rehearsal for individuals and teams</li>
      <li>Rapid access to specialists if needed. Rapid referrals for MRI ultrasound and xrays</li>
    </ul>
  </section>

  <footer class="locations">
    <ul class="location-list">
      <li>Monday,Wednesday, Friday - <strong>KinetaCare</strong> 518 Hollis Rd Hollis, P- <strong>84619027</strong></li>
      <li>Tuesday - <strong>Brackley Sports Clinic</strong> 193 Brackley Rd, Adelaide, P- <strong>81946372</strong></li>
      <li>Thursday - <strong>Riverton Hawks Sports Medicine Clinic</strong> Tolvane Arena, P- <strong>8162 5907</strong></li>
    </ul>
    <div class="brand-tile">
      <span class="brand-mark"></span>
      <span class="brand-name">Peak Stride<br>Athletics</span>
    </div>
  </footer>
  <div class="footer-strip"></div>
</main>
</body>
</html>
```